Single-sided business card for restaurant velmora with new logo made on this site

Business card options with new logo including restaurant name, address, phone number and website. This business card is single-sided only and will be presented at the hostess desk for clients to take. I would like to see options based on a cream card background, a white card background, a yellow card background and a burgundy colored background. It needs to be elegant and traditional.

Target Market(s)

local and international crowd

Industry/Entity Type

restaurant

Contact Information for Business Card

address, website and phone number

Font styles to use
Serif

Colors
EE7325
F08F49
F5BC92
FAE3D3
FDF4ED

Requirements
Must have
• new logo, address, phone number, website
Should not have
• more than three colors

```html
<!DOCTYPE html>
<html lang="es">
<head>
<meta charset="utf-8">
<title>Velmora – Business Card</title>
<link rel="stylesheet" href="https://fonts.googleapis.com/css2?family=Crimson+Pro:wght@400;600&display=swap">
<style>
  :root {
    --page-bg: #ebe6e0;
    --card-dark: #2b2120;
    --card-dark-deep: #1c1514;
    --card-cream: #fdf4ed;
    --leaf-peach: #f5bc92;
    --leaf-blush: #fae3d3;
    --accent: #ee7325;
    --accent-soft: #f08f49;
    --text-light: #ece3da;
    --logo-ink: #1f1817;
  }
  * { margin: 0; padding: 0; box-sizing: border-box; }
  html, body { width: 1200px; height: 969px; overflow: hidden; }
  body {
    background: var(--page-bg);
    font-family: "Crimson Pro", Georgia, serif;
    position: relative;
  }
  .business-card {
    position: absolute;
    left: 100px; top: 200px;
    width: 1000px; height: 570px;
    border-radius: 24px;
    overflow: hidden;
    background: var(--card-cream);
    box-shadow: 0 14px 40px rgba(60, 40, 30, 0.18);
  }
  .card-art { position: absolute; inset: 0; width: 100%; height: 100%; }
  .contact-block {
    position: absolute;
    left: 54px; top: 62px;
    color: var(--text-light);
    font-size: 25px;
    line-height: 32px;
  }
  .contact-label {
    color: var(--accent-soft);
    font-weight: 600;
  }
  .address { margin-bottom: 18px; }
  .phone {
    display: flex; align-items: center; gap: 4px;
    font-size: 31px; line-height: 36px;
  }
  .phone svg { width: 24px; height: 24px; }
  .website {
    margin-top: 14px;
    color: var(--accent-soft);
    font-weight: 600;
    font-size: 25px;
  }
  .brand-mark {
    position: absolute;
    left: 711px; top: 236px;
    width: 146px; height: 146px;
    background: var(--accent);
  }
  .brand-name {
    position: absolute;
    left: 583px; width: 400px; top: 392px;
    text-align: center;
    color: var(--logo-ink);
    font-size: 54px;
    font-weight: 400;
    letter-spacing: 9px;
    line-height: 60px;
  }
  .brand-since {
    position: absolute;
    left: 613px; width: 340px; top: 485px;
    display: flex; align-items: center; gap: 12px;
    color: var(--logo-ink);
    font-size: 13px;
    letter-spacing: 1px;
    text-transform: uppercase;
  }
  .brand-since .rule { flex: 1; height: 2px; background: var(--accent); }
</style>
</head>
<body>
  <div class="business-card">
    <svg class="card-art" viewBox="0 0 1000 570" preserveAspectRatio="none">
      <defs>
        <linearGradient id="darkPanel" x1="0" y1="0" x2="1" y2="1">
          <stop offset="0" stop-color="var(--card-dark)"/>
          <stop offset="1" stop-color="var(--card-dark-deep)"/>
        </linearGradient>
        <radialGradient id="leafGlow" cx="0.62" cy="0.7" r="0.6">
          <stop offset="0" stop-color="var(--leaf-peach)" stop-opacity="0.95"/>
          <stop offset="0.6" stop-color="var(--leaf-blush)" stop-opacity="0.7"/>
          <stop offset="1" stop-color="var(--card-cream)" stop-opacity="0"/>
        </radialGradient>
      </defs>
      <path class="dark-panel" d="M0 0 H660 C600 200 520 390 470 570 H0 Z" fill="url(#darkPanel)"/>
      <rect class="leaf-illustration" role="img" aria-label="Large agave leaf illustration in soft peach tones fanning across the card" x="320" y="80" width="680" height="490" fill="url(#leafGlow)"/>
    </svg>

    <div class="contact-block">
      <p class="contact-label">Restaurant Velmora</p>
      <p class="address">Camelia 415<br>Bahías de Santa Lucía<br>Oaxaca CP 70412</p>
      <p class="contact-label">Reservaciones</p>
      <p class="phone">
        <svg viewBox="0 0 24 24" aria-hidden="true"><path d="M6.6 3.5l3 3.2-1.8 2.3c1.2 2.6 3.2 4.6 5.8 5.8l2.3-1.8 3.2 3-1.6 3.2C12 18.7 5.3 12 5 4.9z" fill="none" stroke="var(--text-light)" stroke-width="1.5" stroke-linejoin="round"/></svg>
        958-555-0142
      </p>
      <p class="website">Velmora.com.mx</p>
    </div>

    <div class="brand-mark" aria-hidden="true"></div>
    <p class="brand-name">VELMORA</p>
    <div class="brand-since"><span class="rule"></span><span>Desde 1999</span><span class="rule"></span></div>
  </div>
</body>
</html>
```